Business Card Design for Varomir Facility Services

We are looking for a Business Card Design for the Company "Varomir Facility Services."
Front side:
- Company Logo (small)
- Company Name, address, pohone, website and personal data.
- white background, for text e.g. company colors (blue or green like in the logo)
Please use following data:
Company data:
Varomir Facility Services Kostelac
Birkenhaldweg 14
8816 Lindwiler
www.varomir-fs.ch
Person data:
Tarik Kostelac
Geschäftsführer
+41 76 519 47 83
info@varomir-fs.ch
Back side:
could be colored in blue or green
please use a big logo sing and some smaller icons to say what is all beeing offered in facility services, like cleaning, maintenance cleaning
industrial cleaning, caretaking, gardening, disposal. There is no need for everyone of the icons if there are similar or an icon is standing for more of them.
colors to use:
blue: HEX 246BB0
green: HEX 52B33E

```html
<!DOCTYPE html>
<html lang="de">
<head>
<meta charset="utf-8">
<title>Varomir Facility Services – Business Card</title>
<link href="https://fonts.googleapis.com/css2?family=Roboto:wght@400;500;700&display=swap" rel="stylesheet">
<style>
  :root {
    --blue: #246BB0;
    --green: #52B33E;
    --green-deep: #14a44a;
    --green-light: #8ccc52;
    --teal: #13908e;
    --white: #ffffff;
    --stage: #e6e8e6;
  }
  * { box-sizing: border-box; margin: 0; padding: 0; }
  html, body { width: 1200px; height: 900px; overflow: hidden; }
  body {
    background: var(--stage);
    font-family: "Roboto", Arial, sans-serif;
    display: flex;
    flex-direction: column;
    align-items: center;
    justify-content: center;
    gap: 36px;
  }
  .card {
    position: relative;
    width: 700px;
    height: 400px;
    border-radius: 22px;
    overflow: hidden;
    box-shadow: 0 6px 18px rgba(0,0,0,.18);
  }

  /* Back side */
  .card-back {
    background: linear-gradient(30deg, #3d72bf 0%, var(--teal) 35%, #3fae4f 70%, var(--green-light) 100%);
    color: var(--white);
  }
  .back-brand {
    position: absolute;
    top: 70px; left: 0; right: 0;
    text-align: center;
  }
  .back-brand .brand-name {
    font-weight: 500;
    font-size: 62px;
    letter-spacing: 6px;
    text-transform: uppercase;
    line-height: 1;
  }
  .back-brand .brand-sub {
    font-weight: 500;
    font-size: 22px;
    letter-spacing: 8px;
    text-transform: uppercase;
    margin-top: 10px;
  }
  .services {
    position: absolute;
    left: 30px; right: 30px; bottom: 52px;
    display: flex;
    justify-content: space-between;
    list-style: none;
  }
  .service {
    width: 100px;
    text-align: center;
    font-size: 13px;
    line-height: 1.2;
  }
  .service-icon {
    display: block;
    width: 46px; height: 46px;
    margin: 0 auto 10px;
    border-radius: 50%;
    background: rgba(255,255,255,.85);
  }

  /* Front side */
  .card-front { background: var(--white); }
  .front-band { position: absolute; inset: 0; }
  .front-brand {
    position: absolute;
    top: 100px; left: 48px;
    display: flex; align-items: center; gap: 12px;
    color: var(--blue);
    font-weight: 500;
    font-size: 26px;
    letter-spacing: 1px;
  }
  .front-brand .brand-dot {
    width: 22px; height: 22px; border-radius: 50%; background: var(--blue);
  }
  .company {
    position: absolute;
    top: 172px; left: 48px;
    color: var(--blue);
    font-size: 17px;
    line-height: 1.35;
  }
  .company .company-name { font-weight: 700; font-size: 19px; }
  .company .accent { color: var(--green); }
  .company .web {
    display: flex; align-items: center; gap: 6px;
    color: var(--green); font-weight: 700; margin-top: 2px;
  }
  .person {
    position: absolute;
    right: 30px; top: 222px;
    color: var(--white);
    text-align: right;
  }
  .person .person-name { font-weight: 700; font-size: 22px; letter-spacing: .5px; }
  .person .person-role { font-size: 15px; letter-spacing: 1px; margin-top: 2px; }
  .contacts {
    position: absolute;
    right: 30px; bottom: 36px;
    display: flex; gap: 22px;
    color: var(--white);
    font-size: 15px;
  }
  .contact { display: flex; align-items: center; gap: 7px; }
</style>
</head>
<body>

  <section class="card card-back" aria-label="Back side">
    <div class="back-brand">
      <div class="brand-name">Varomir</div>
      <div class="brand-sub">Facility Services</div>
    </div>
    <ul class="services">
      <li class="service"><span class="service-icon" role="img" aria-label="Cleaning icon"></span>Cleaning</li>
      <li class="service"><span class="service-icon" role="img" aria-label="Maintenance cleaning icon"></span>Maintenance cleaning</li>
      <li class="service"><span class="service-icon" role="img" aria-label="Industrial cleaning icon"></span>Industrial cleaning</li>
      <li class="service"><span class="service-icon" role="img" aria-label="Caretaking icon"></span>Caretaking</li>
      <li class="service"><span class="service-icon" role="img" aria-label="Gardening icon"></span>Gardening</li>
      <li class="service"><span class="service-icon" role="img" aria-label="Disposal icon"></span>Disposal</li>
    </ul>
  </section>

  <section class="card card-front" aria-label="Front side">
    <svg class="front-band" viewBox="0 0 700 400" width="700" height="400" aria-hidden="true">
      <defs>
        <linearGradient id="bandFill" x1="0" y1="1" x2="1" y2="0">
          <stop offset="0" stop-color="#14a44a"/>
          <stop offset="1" stop-color="#8ccc52"/>
        </linearGradient>
      </defs>
      <polygon points="0,400 700,110 700,400" fill="url(#bandFill)"/>
      <line x1="0" y1="390" x2="700" y2="100" stroke="#246BB0" stroke-width="3"/>
    </svg>

    <div class="front-brand"><span class="brand-dot"></span>Varomir Facility Services</div>

    <div class="company">
      <div class="company-name">Varomir <span class="accent">Facility Services</span> Kostelac</div>
      <div>Birkenhaldweg 14</div>
      <div>8816 Lindwiler</div>
      <div class="web">
        <svg width="16" height="16" viewBox="0 0 16 16" aria-hidden="true"><g fill="none" stroke="#52B33E" stroke-width="1.4"><circle cx="8" cy="8" r="6.5"/><ellipse cx="8" cy="8" rx="3" ry="6.5"/><path d="M1.5 8h13M2.5 4.8h11M2.5 11.2h11"/></g></svg>
        www.varomir-fs.ch
      </div>
    </div>

    <div class="person">
      <div class="person-name">TARIK KOSTELAC</div>
      <div class="person-role">GESCHÄFTSFÜHRER</div>
    </div>

    <div class="contacts">
      <div class="contact">
        <svg width="20" height="20" viewBox="0 0 20 20" aria-hidden="true"><circle cx="10" cy="10" r="10" fill="#fff"/><path d="M7 5.5c.6 0 1.3 1.6 1.3 2.1s-.8.8-.8 1.3c.4 1.2 1.5 2.3 2.7 2.7.5 0 .8-.8 1.3-.8s2.1.7 2.1 1.3c0 .9-1 1.9-2 1.9C8.6 14 6 11.4 5.1 8.4 5.1 7.4 6.1 5.5 7 5.5z" fill="#52B33E"/></svg>
        +41 76 519 47 83
      </div>
      <div class="contact">
        <svg width="20" height="20" viewBox="0 0 20 20" aria-hidden="true"><circle cx="10" cy="10" r="10" fill="#fff"/><rect x="5" y="6.5" width="10" height="7" fill="none" stroke="#52B33E" stroke-width="1.3"/><path d="M5 6.5l5 4 5-4" fill="none" stroke="#52B33E" stroke-width="1.3"/></svg>
        info@varomir-fs.ch
      </div>
    </div>
  </section>

</body>
</html>
```